Quendle Pools & Patio Homepage Design

I am looking for someone to design a one-page website for a company called Quendle Pools & Patio. While the content will be different, the design should be similar to https://quendle-example.com/pools-patio/.
Industry/Entity Type
Pool Cleaning Service
Number of Pages Required
1 page
Font styles to use
Other font styles liked:
- See brand guidelines

Requirements
Must have
- Must be similar in style https://quendle-example.com/pools-patio/. Look at the Word Doc for the content.

```html
<!DOCTYPE html>
<html lang="en">
<head>
<meta charset="utf-8">
<title>Quendle Pools &amp; Patio</title>
<link rel="stylesheet" href="https://fonts.googleapis.com/css2?family=Comfortaa:wght@400;500;700&family=Heebo:wght@300;400;500;700&family=Roboto+Condensed:wght@700&family=Lora:wght@700&display=swap">
<style>
:root{
  --green:#2bd45f;
  --green-dark:#1fb84f;
  --blue:#3a93dc;
  --blue-light:#4aa3e6;
  --ink:#222;
  --text:#666;
  --line:#d6d6d6;
  --dark:#262626;
  --white:#fff;
}
*{box-sizing:border-box;margin:0;padding:0}
html,body{width:1200px;height:4637px;overflow:hidden}
body{position:relative;background:var(--white);font-family:"Heebo",sans-serif;color:var(--text)}
.abs{position:absolute}
.brand{display:flex;align-items:center;gap:14px;font-family:"Comfortaa",sans-serif;font-weight:700;color:var(--green)}
.brand-mark{background:var(--green);border-radius:6px}

/* header */
.site-header{position:absolute;left:0;top:0;width:1200px;height:103px;background:var(--white)}
.site-header .brand{position:absolute;left:112px;top:24px;font-size:46px}
.site-header .brand-mark{width:48px;height:48px}
.main-nav{position:absolute;left:423px;top:42px;display:flex;gap:26px;font-size:14px;font-weight:700;color:var(--ink)}
.main-nav .active{color:var(--blue)}
.btn{display:inline-flex;align-items:center;justify-content:center;color:var(--white);font-weight:700;font-size:13px;text-transform:uppercase}
.btn-signin{position:absolute;left:873px;top:34px;width:95px;height:38px;background:var(--green)}
.btn-quote{position:absolute;left:979px;top:34px;width:110px;height:38px;background:var(--blue)}

/* hero */
.hero-media{position:absolute;left:0;top:103px;width:1200px;height:700px;background:linear-gradient(180deg,#7fa6c9 0%,#5c8a4e 30%,#8a7660 55%,#2aa6e0 80%,#5fc4ef 100%)}
.slider-arrow{position:absolute;top:385px;width:46px;height:46px;border-radius:50%;background:var(--white);display:flex;align-items:center;justify-content:center}
.hero-edge{position:absolute;left:0;top:700px}
.quote-card{position:absolute;left:252px;top:659px;width:697px;height:280px;background:var(--white);text-align:center}
.quote-card h1{font-family:"Comfortaa",sans-serif;font-weight:400;color:var(--blue);font-size:40px;line-height:52px;margin-top:26px}
.field{position:absolute;height:44px;border:1px solid var(--line);font-size:13px;color:#777;display:flex;align-items:center;padding-left:20px;background:var(--white)}
.btn-submit{position:absolute;height:44px;background:var(--green);color:var(--white);font-size:13px;font-weight:700;display:flex;align-items:center;justify-content:center}

/* overview */
.hex{clip-path:polygon(50% 0,100% 25%,100% 75%,50% 100%,0 75%,0 25%)}
.overview-hex{left:139px;top:959px;width:394px;height:463px;background:var(--green)}
.overview-photo{left:161px;top:1000px;width:350px;height:382px;background:linear-gradient(180deg,#c9b59a 0%,#8a6a52 45%,#4f9cbf 70%,#8cc6da 100%)}
.section-title{font-family:"Comfortaa",sans-serif;font-weight:500;color:var(--ink)}
.overview-title{left:576px;top:1002px;font-size:42px}
.overview-copy{left:576px;top:1070px;width:465px;font-size:13.4px;line-height:25.6px;text-align:justify;font-weight:300;color:#555}
.overview-copy p+p{margin-top:26px}

/* services */
.services-band{left:0;top:1472px;width:1200px;height:523px;background:linear-gradient(100deg,var(--green) 0%,#2ec38f 50%,var(--blue) 100%)}
.services-title{left:0;top:1598px;width:1200px;text-align:center;color:var(--white);font-size:42px}
.service-hex-frame{top:1688px;width:304px;height:324px;background:var(--white)}
.service-hex-photo{position:absolute;left:10px;top:11px;width:284px;height:302px}
.service-name{top:2030px;width:304px;text-align:center;font-family:"Lora",serif;font-weight:700;font-size:20px;color:var(--ink)}
.service-text{top:2066px;width:254px;font-size:13px;line-height:21.6px;color:#666;font-weight:300}

/* technician */
.tech-title{left:0;top:2266px;width:1200px;text-align:center;font-size:42px}
.tech-quote{left:158px;top:2428px;width:576px;height:261px;background:var(--blue);color:var(--white);text-align:right;padding:36px 36px 0 50px}
.tech-quote p{font-size:21px;line-height:34.5px;font-weight:300}
.tech-quote .tech-name{font-family:"Roboto Condensed",sans-serif;font-weight:700;font-size:30px;margin-top:14px}
.quote-glyph{left:224px;top:2660px;font-family:"Lora",serif;font-size:90px;line-height:1;color:var(--green);font-weight:700}
.tech-photo{left:733px;top:2353px;width:311px;height:401px;background:linear-gradient(180deg,#d9d9d9 0%,#c4c4c4 50%,#3b3f4a 80%,#2c3038 100%)}

/* service area */
.area-band{left:0;top:2871px;width:1200px;height:720px;background:linear-gradient(110deg,var(--green) 0%,#2ec38f 45%,var(--blue) 100%)}
.area-title{left:182px;top:3052px;font-size:42px;color:var(--white)}
.area-list{left:182px;top:3150px;list-style:none;color:var(--white);font-family:"Comfortaa",sans-serif;font-size:26px}
.area-list li{display:flex;align-items:center;gap:18px;height:51.5px}
.area-map{left:549px;top:2970px;width:472px;height:450px;border-radius:28px;background:radial-gradient(ellipse at 55% 55%,rgba(255,255,255,.32),rgba(255,255,255,.06) 75%)}

/* contact */
.contact-title{left:0;top:3662px;width:1200px;text-align:center;font-size:42px}
.contact-item{left:146px;display:flex;gap:20px;align-items:flex-start}
.contact-icon{width:68px;height:68px;border-radius:50%;border:3px solid var(--green);display:flex;align-items:center;justify-content:center;flex:none}
.contact-icon span{width:54px;height:54px;border-radius:50%;background:var(--green);display:flex;align-items:center;justify-content:center}
.contact-item p{font-size:15px;line-height:26px;color:#444;margin-top:4px}
.cfield{position:absolute;height:56px;border:1px solid var(--line);font-size:12.5px;color:#777;display:flex;align-items:center;padding-left:22px}
.method-label{left:486px;top:3911px;font-size:12.5px;font-weight:500;color:#444}
.method{top:3947px;display:flex;align-items:center;gap:20px;font-size:12.5px;color:#444}
.method-box{width:34px;height:34px;background:#e6e6e6;display:flex;align-items:center;justify-content:center}
.contact-submit{left:488px;top:4010px;width:174px;height:38px;background:var(--blue);color:var(--white);font-size:14px;font-weight:500;display:flex;align-items:center;justify-content:center}

/* footer */
.footer-band{left:0;top:4290px;width:1200px;height:347px;background:var(--dark)}
.site-footer .brand{left:124px;top:4330px;font-size:54px}
.site-footer .brand-mark{width:56px;height:56px}
.footer-about{left:124px;top:4420px;width:320px;font-size:14px;line-height:26px;color:#eee}
.footer-heading{top:4312px;font-size:21px;font-weight:700;color:var(--white)}
.footer-links{left:554px;top:4360px;list-style:none;font-size:14px;color:#eee}
.footer-links li{height:26px;display:flex;align-items:center;gap:14px}
.footer-links li::before{content:"»";color:var(--green)}
.footer-contact{left:828px;top:4360px;list-style:none;font-size:14px;color:#eee;line-height:26px}
.footer-contact li{display:flex;gap:22px;margin-bottom:26px;width:260px}
.footer-contact svg{flex:none;margin-top:6px}
.copyright{left:0;top:4563px;width:1200px;text-align:center;font-size:13px;color:#ccc}
</style>
</head>
<body>

<header class="site-header">
  <div class="brand"><span class="brand-mark"></span>quendle</div>
  <nav class="main-nav">
    <span class="active">Home</span><span>About</span><span>Services</span><span>Learn</span><span>Locations</span><span>FAQs</span>
  </nav>
  <span class="btn btn-signin">Signin</span>
  <span class="btn btn-quote">Get a Quote</span>
</header>

<section class="hero">
  <div class="hero-media" role="img" aria-label="Backyard swimming pool with a yellow slide, flowering shrubs and a wooden fence"></div>
  <svg class="hero-edge" width="1200" height="110" viewBox="0 0 1200 110">
    <polygon points="0,28 252,60 252,110 0,110" fill="#fff"/>
    <polygon points="0,20 252,58 252,92 0,52" fill="var(--green)"/>
    <polygon points="949,70 1200,42 1200,110 949,110" fill="#fff"/>
    <polygon points="949,60 1200,30 1200,52 949,84" fill="var(--blue)"/>
  </svg>
  <span class="slider-arrow" style="left:66px"><svg width="14" height="14" viewBox="0 0 14 14"><path d="M9 2 4 7l5 5" stroke="#222" stroke-width="2" fill="none"/></svg></span>
  <span class="slider-arrow" style="left:1088px"><svg width="14" height="14" viewBox="0 0 14 14"><path d="m5 2 5 5-5 5" stroke="#222" stroke-width="2" fill="none"/></svg></span>
  <div class="quote-card">
    <h1>Keep Your Pool<br>Sparkling With Quendle!</h1>
  </div>
  <div class="field" style="left:288px;top:810px;width:202px">Name</div>
  <div class="field" style="left:499px;top:810px;width:203px">Email</div>
  <div class="field" style="left:711px;top:810px;width:203px">Phone</div>
  <div class="field" style="left:288px;top:864px;width:414px">Preferred Contact Method
    <svg style="position:absolute;right:20px" width="10" height="6" viewBox="0 0 10 6"><path d="m1 1 4 4 4-4" stroke="#777" fill="none"/></svg></div>
  <div class="btn-submit" style="left:711px;top:864px;width:203px">SUBMIT NOW</div>
</section>

<section class="overview">
  <div class="abs hex overview-hex"></div>
  <div class="abs hex overview-photo" role="img" aria-label="Technician cleaning a pool with a skimmer pole beside a house"></div>
  <h2 class="abs section-title overview-title">Company Overview</h2>
  <div class="abs overview-copy">
    <p>We're Quendle Pools &amp; Patio, and we specialize in pool cleaning and repair services that will keep your pool looking its best. Our reliable and professional team is committed to helping you get the most out of your backyard oasis, ensuring it's always ready for all types of fun when you want it. Our weekly pool cleaning service is affordable and ensures that your pool is properly taken care of throughout the swimming season.</p>
    <p>When you choose us as your go-to for all things pools, relaxing days spent on a clean lounge chair are worry-free because we take care of all the hard work! From chemical balancing to scrubbing and filter maintenance - there's nothing too big or small for us. So don't wait any longer - trust Quendle to keep your pool sparkling all summer!</p>
  </div>
</section>

<section class="services">
  <div class="abs services-band"></div>
  <svg class="abs" style="left:0;top:1470px" width="1200" height="120" viewBox="0 0 1200 120">
    <polygon points="0,0 1200,0 1200,112 600,2 0,112" fill="#fff"/>
    <polygon points="0,112 600,2 1200,112 1200,140 600,36 0,140" fill="var(--blue)"/>
  </svg>
  <h2 class="abs section-title services-title">Our Services</h2>

  <div class="abs hex service-hex-frame" style="left:112px"><div class="hex service-hex-photo" style="background:linear-gradient(160deg,#5b4a3a,#c9c2b5 50%,#7a6048)" role="img" aria-label="Technician holding a pool filter cartridge"></div></div>
  <div class="abs hex service-hex-frame" style="left:448px"><div class="hex service-hex-photo" style="background:linear-gradient(180deg,#3c5a2e 0%,#8c7a5a 40%,#2fa3dc 60%,#8fd3f2 100%)" role="img" aria-label="Clean pool with lounge chairs"></div></div>
  <div class="abs hex service-hex-frame" style="left:785px"><div class="hex service-hex-photo" style="background:linear-gradient(150deg,#32b6e6,#7ad4f2 50%,#1f8fcc)" role="img" aria-label="Pool vacuum hose coiled in blue water"></div></div>

  <h3 class="abs service-name" style="left:112px">Pool Cleaning</h3>
  <h3 class="abs service-name" style="left:448px">Pool Maintenance</h3>
  <h3 class="abs service-name" style="left:785px">Pool Repair</h3>
  <p class="abs service-text" style="left:137px;text-align:justify;text-align-last:center">Our weekly service includes chemical balancing, debris removal, wall and step scrubbing, and filter maintenance. Standard chemicals are included in the quoted price.</p>
  <p class="abs service-text" style="left:473px;text-align:center">We perform regular checks on all your pool equipment to make sure it runs efficiently and safely.</p>
  <p class="abs service-text" style="left:810px;text-align:center">From plumbing to equipment malfunctions, our qualified technicians can diagnose and repair any pool problem you may have.</p>
</section>

<section class="technician">
  <h2 class="abs section-title tech-title">Meet Your Technician</h2>
  <div class="abs tech-quote">
    <p>"I understand that keeping your pool clean and<br>well-maintained is a priority for you, which is why I'm<br>committed to providing top-notch pool cleaning and<br>repair services. Let's get started!"</p>
    <div class="tech-name">Dale Harmon</div>
  </div>
  <div class="abs quote-glyph">“</div>
  <div class="abs tech-photo" role="img" aria-label="Portrait of the pool technician in a plaid shirt"></div>
</section>

<section class="service-area">
  <div class="abs area-band"></div>
  <svg class="abs" style="left:0;top:3460px" width="1200" height="135" viewBox="0 0 1200 135">
    <polygon points="0,0 600,112 1200,0 1200,135 0,135" fill="#fff"/>
    <polygon points="0,0 600,104 1200,0 1200,26 600,132 0,26" fill="var(--blue)"/>
  </svg>
  <h2 class="abs section-title area-title">Service Area</h2>
  <ul class="abs area-list">
    <li><svg width="22" height="22" viewBox="0 0 22 22"><circle cx="11" cy="11" r="11" fill="#fff"/><path d="m6 11 3.5 3.5L16 8" stroke="var(--green)" stroke-width="2.6" fill="none"/></svg>Argyle</li>
    <li><svg width="22" height="22" viewBox="0 0 22 22"><circle cx="11" cy="11" r="11" fill="#fff"/><path d="m6 11 3.5 3.5L16 8" stroke="var(--green)" stroke-width="2.6" fill="none"/></svg>Corinth</li>
    <li><svg width="22" height="22" viewBox="0 0 22 22"><circle cx="11" cy="11" r="11" fill="#fff"/><path d="m6 11 3.5 3.5L16 8" stroke="var(--green)" stroke-width="2.6" fill="none"/></svg>Flower Mound</li>
    <li><svg width="22" height="22" viewBox="0 0 22 22"><circle cx="11" cy="11" r="11" fill="#fff"/><path d="m6 11 3.5 3.5L16 8" stroke="var(--green)" stroke-width="2.6" fill="none"/></svg>Lewisville</li>
  </ul>
  <div class="abs area-map" role="img" aria-label="Map of the state marking the service area locations"></div>
</section>

<section class="contact">
  <h2 class="abs section-title contact-title">Contact Us</h2>
  <div class="abs contact-item" style="top:3755px">
    <div class="contact-icon"><span><svg width="20" height="24" viewBox="0 0 20 24"><path d="M10 1a8 8 0 0 0-8 8c0 6 8 14 8 14s8-8 8-14a8 8 0 0 0-8-8z" fill="#fff"/><circle cx="10" cy="9" r="3" fill="var(--green)"/></svg></span></div>
    <p>123, Lorem ipsum dolor<br>amet, consectetur</p>
  </div>
  <div class="abs contact-item" style="top:3867px">
    <div class="contact-icon"><span><svg width="22" height="22" viewBox="0 0 24 24"><path d="M6.6 10.8a15 15 0 0 0 6.6 6.6l2.2-2.2a1 1 0 0 1 1-.3 11 11 0 0 0 3.6.6 1 1 0 0 1 1 1V20a1 1 0 0 1-1 1A17 17 0 0 1 3 4a1 1 0 0 1 1-1h3.5a1 1 0 0 1 1 1 11 11 0 0 0 .6 3.6 1 1 0 0 1-.3 1z" fill="#fff"/></svg></span></div>
    <p>Phone :<br>555-014-2286</p>
  </div>
  <div class="abs contact-item" style="top:3978px">
    <div class="contact-icon"><span><svg width="22" height="16" viewBox="0 0 22 16"><rect width="22" height="16" rx="2" fill="#fff"/><path d="m1 2 10 7 10-7" stroke="var(--green)" stroke-width="2" fill="none"/></svg></span></div>
    <p>Email :<br>info@quendle-example.com</p>
  </div>

  <div class="cfield" style="left:486px;top:3760px;width:275px">First name</div>
  <div class="cfield" style="left:776px;top:3760px;width:275px">Last name</div>
  <div class="cfield" style="left:486px;top:3830px;width:275px">Email</div>
  <div class="cfield" style="left:776px;top:3830px;width:275px">Phone</div>
  <div class="abs method-label">Preferred Contact Method</div>
  <div class="abs method" style="left:486px"><span class="method-box"><svg width="12" height="12" viewBox="0 0 24 24"><path d="M6.6 10.8a15 15 0 0 0 6.6 6.6l2.2-2.2a1 1 0 0 1 1-.3 11 11 0 0 0 3.6.6 1 1 0 0 1 1 1V20a1 1 0 0 1-1 1A17 17 0 0 1 3 4a1 1 0 0 1 1-1h3.5a1 1 0 0 1 1 1 11 11 0 0 0 .6 3.6 1 1 0 0 1-.3 1z" fill="#555"/></svg></span>Call</div>
  <div class="abs method" style="left:632px"><span class="method-box"><svg width="12" height="12" viewBox="0 0 12 12"><rect width="12" height="12" fill="#555"/><path d="M3 9l1-3 4-4 2 2-4 4z" fill="#e6e6e6"/></svg></span>Text</div>
  <div class="abs method" style="left:778px"><span class="method-box"><svg width="13" height="10" viewBox="0 0 13 10"><rect width="13" height="10" fill="#555"/><path d="m1 1 5.5 4L12 1" stroke="#e6e6e6" fill="none"/></svg></span>Email</div>
  <div class="abs contact-submit">Submit Now</div>
</section>

<footer class="site-footer">
  <div class="abs footer-band"></div>
  <svg class="abs" style="left:0;top:4145px" width="1200" height="150" viewBox="0 0 1200 150">
    <defs><linearGradient id="footerEdge" x1="0" x2="1"><stop offset="0" stop-color="#2bd45f"/><stop offset="1" stop-color="#3a93dc"/></linearGradient></defs>
    <polygon points="0,115 600,4 1200,115 1200,150 0,150" fill="url(#footerEdge)"/>
    <polygon points="0,140 600,40 1200,140 1200,150 0,150" fill="var(--dark)"/>
  </svg>
  <div class="abs brand"><span class="brand-mark"></span>quendle</div>
  <p class="abs footer-about">Lorem ipsum dolor sit amet, consectetur adipi scing elit, sed do eiusmod tempor incidid unt ut labore et dolore magna aliqua.</p>
  <h4 class="abs footer-heading" style="left:554px">Quick Links</h4>
  <ul class="abs footer-links">
    <li>Home</li><li>About us</li><li>Services</li><li>Reviews</li><li>News</li><li>Contact us</li>
  </ul>
  <h4 class="abs footer-heading" style="left:828px">Contact us</h4>
  <ul class="abs footer-contact">
    <li><svg width="10" height="13" viewBox="0 0 20 24"><path d="M10 1a8 8 0 0 0-8 8c0 6 8 14 8 14s8-8 8-14a8 8 0 0 0-8-8z" fill="var(--green)"/></svg>Lorem ipsum dolor sit amet, cons ectetur adipiscing</li>
    <li><svg width="12" height="12" viewBox="0 0 24 24"><path d="M6.6 10.8a15 15 0 0 0 6.6 6.6l2.2-2.2a1 1 0 0 1 1-.3 11 11 0 0 0 3.6.6 1 1 0 0 1 1 1V20a1 1 0 0 1-1 1A17 17 0 0 1 3 4a1 1 0 0 1 1-1h3.5a1 1 0 0 1 1 1 11 11 0 0 0 .6 3.6 1 1 0 0 1-.3 1z" fill="var(--green)"/></svg>555-014-2286</li>
    <li><svg width="13" height="10" viewBox="0 0 13 10"><rect width="13" height="10" fill="var(--green)"/><path d="m1 1 5.5 4L12 1" stroke="var(--dark)" fill="none"/></svg>info@quendle-example.com</li>
  </ul>
  <p class="abs copyright">© Copyrights 2023 Company name | All Rights reserved</p>
</footer>

</body>
</html>
```